New Company Business Card design

Looking for a corporate looking business card utilising my new logo design - the logo i would like embossed as one option and flat as another - simplistic but stylish - less is more - we are an import export business launching into the market - i would like a couple of options as main background - Grey or Black

```html
<!DOCTYPE html>
<html lang="en">
<head>
<meta charset="utf-8">
<title>Northvale Trade Group – Business Card</title>
<link href="https://fonts.googleapis.com/css2?family=Cinzel:wght@400;500&family=Roboto:wght@400;500&display=swap" rel="stylesheet">
<style>
  :root {
    --stage: #2b2b2d;
    --card: #0b0b0c;
    --card-sheen: #1a1a1c;
    --brand-blue: #2f8fd8;
    --soft-white: #e9e9ea;
    --muted-grey: #a9a9ad;
    --rule: #8c8c90;
  }
  * { box-sizing: border-box; margin: 0; padding: 0; }
  html, body { width: 1200px; height: 896px; overflow: hidden; }
  body {
    background: var(--stage);
    display: flex;
    align-items: center;
    justify-content: center;
    gap: 48px;
    font-family: "Roboto", Arial, sans-serif;
  }
  .card {
    position: relative;
    width: 540px;
    height: 309px;
    border-radius: 18px;
    background: linear-gradient(135deg, var(--card-sheen) 0%, var(--card) 55%);
    overflow: hidden;
  }
  .brand {
    display: flex;
    flex-direction: column;
    align-items: flex-start;
  }
  .brand-row { display: flex; align-items: center; gap: 12px; }
  .brand-dot {
    width: 22px; height: 22px; border-radius: 50%;
    background: var(--brand-blue);
  }
  .brand-name {
    font-family: "Cinzel", Georgia, serif;
    font-weight: 500;
    color: var(--brand-blue);
    letter-spacing: 0.04em;
    white-space: nowrap;
  }
  .brand-tagline {
    margin-top: 6px;
    padding: 4px 0;
    border-top: 1px solid var(--rule);
    border-bottom: 1px solid var(--rule);
    font-family: "Cinzel", Georgia, serif;
    color: var(--muted-grey);
    letter-spacing: 0.14em;
    white-space: nowrap;
  }
  /* front */
  .card-front { display: flex; align-items: center; justify-content: center; }
  .card-front .brand-name { font-size: 24px; }
  .card-front .brand-tagline { font-size: 10.5px; align-self: stretch; text-align: center; }
  /* back */
  .card-back .brand { position: absolute; left: 34px; bottom: 44px; }
  .card-back .brand-name { font-size: 19px; }
  .card-back .brand-dot { width: 18px; height: 18px; }
  .card-back .brand-tagline { font-size: 8.5px; align-self: stretch; text-align: center; }
  .contact {
    position: absolute;
    top: 34px;
    right: 34px;
    width: 230px;
    padding-left: 20px;
    border-left: 1px solid var(--rule);
    color: var(--soft-white);
  }
  .contact-name {
    font-size: 19px; font-weight: 500;
    color: var(--brand-blue);
    text-transform: uppercase;
    letter-spacing: 0.02em;
  }
  .contact-role { font-size: 12px; margin: 2px 0 12px; }
  .contact-address { font-size: 12px; line-height: 1.45; margin-bottom: 10px; }
  .contact-line {
    display: flex; align-items: center; gap: 8px;
    font-size: 12px; line-height: 1.6;
  }
  .contact-line svg { width: 10px; height: 10px; flex: none; }
  .web-accent { color: var(--brand-blue); }
</style>
</head>
<body>
  <section class="card card-front" aria-label="Business card front">
    <div class="brand">
      <div class="brand-row">
        <span class="brand-dot"></span>
        <span class="brand-name">Northvale Trade Group</span>
      </div>
      <span class="brand-tagline">Worldwide Supply for Every Market</span>
    </div>
  </section>

  <section class="card card-back" aria-label="Business card back">
    <div class="contact">
      <p class="contact-name">Daniel Hart</p>
      <p class="contact-role">Director</p>
      <p class="contact-address">2250 Orchard Valley Rd<br>Alder, CA 95120-4410</p>
      <p class="contact-line">
        <svg viewBox="0 0 10 10"><path d="M2 1 L4 1 L4.6 3 L3.4 3.8 Q4.4 5.8 6.2 6.6 L7 5.4 L9 6 L9 8 Q5 9 2.4 6 Q1 4 2 1Z" fill="var(--soft-white)"/></svg>
        555-204-7731
      </p>
      <p class="contact-line">
        <svg viewBox="0 0 10 10"><rect x="0.5" y="2" width="9" height="6.5" fill="none" stroke="var(--brand-blue)"/><path d="M0.5 2 L5 5.6 L9.5 2" fill="none" stroke="var(--brand-blue)"/></svg>
        info@northvale-trade.com
      </p>
      <p class="contact-line">
        <svg viewBox="0 0 10 10"><circle cx="5" cy="5" r="4.3" fill="none" stroke="var(--soft-white)"/><path d="M0.7 5 H9.3 M5 0.7 Q2.5 5 5 9.3 M5 0.7 Q7.5 5 5 9.3" fill="none" stroke="var(--soft-white)" stroke-width="0.7"/></svg>
        <span>www.<span class="web-accent">northvale-trade</span>.com</span>
      </p>
    </div>
    <div class="brand">
      <div class="brand-row">
        <span class="brand-dot"></span>
        <span class="brand-name">Northvale Trade Group</span>
      </div>
      <span class="brand-tagline">Worldwide Supply for Every Market</span>
    </div>
  </section>
</body>
</html>
```